Quorva - corporate Business Card

We need a good look and innovative business card for a new start up company based in Los Angeles called "Quorva". We are in a payment business, including payment card, app, and ewallet. We are expert in online payment and Card not present (CNP) transaction.
We need an innovative, modern business card.

Our logo font is Aero Matics

Target Market(s)

Startup - Bank - Online Payment - Card Manufacturing

Industry/Entity Type

Startup

Contact Information for Business Card

phone: 555 014 7396 - Address: 4172 Marlowe blvd, Fernhollow, CA 90299

Requirements
Must have
• Message: innovative, professional, expert, high tech, trust, online payment expert, security
Nice to have
• no comment
Should not have
• no Comment

```html
<!DOCTYPE html>
<html lang="en">
<head>
<meta charset="utf-8">
<title>Quorva — Business Card</title>
<link rel="stylesheet" href="https://fonts.googleapis.com/css2?family=Exo+2:wght@500&family=Lato:wght@400;700&display=swap">
<style>
  :root {
    --stage: #ece9e6;
    --card-dark: #000000;
    --brand-red: #b81f2e;
    --brand-red-deep: #a91b29;
    --ink-light: #ffffff;
    --ink-muted: #d6d6d6;
  }
  * { margin: 0; padding: 0; box-sizing: border-box; }
  html, body { width: 1200px; height: 900px; overflow: hidden; }
  body {
    position: relative;
    background: var(--stage);
    font-family: "Lato", Arial, sans-serif;
  }
  .card { position: absolute; overflow: hidden; box-shadow: 0 4px 14px rgba(0,0,0,.18); }

  /* Front card */
  .card--front {
    left: 77px; top: 35px; width: 588px; height: 362px;
    background: var(--card-dark);
  }
  .brand { position: absolute; display: flex; align-items: center; }
  .brand__dot { border-radius: 50%; flex: none; }
  .brand__name {
    font-family: "Exo 2", "Lato", sans-serif;
    font-weight: 500;
    letter-spacing: 1px;
    line-height: 1;
  }
  .card--front .brand { left: 133px; top: 78px; }
  .card--front .brand__dot { width: 94px; height: 94px; background: var(--brand-red); margin-right: 14px; }
  .card--front .brand__name { font-size: 64px; color: var(--brand-red); padding-bottom: 10px; }

  .person { position: absolute; right: 310px; top: 236px; text-align: right; }
  .person__name { color: var(--brand-red); font-weight: 700; font-size: 19px; line-height: 1.1; }
  .person__role { color: var(--ink-muted); font-size: 16px; margin-top: 4px; }

  .contact { position: absolute; left: 298px; top: 236px; list-style: none; }
  .contact__item { display: flex; align-items: center; color: var(--ink-muted); font-size: 16px; height: 22px; }
  .contact__icon { width: 12px; height: 12px; margin-right: 13px; fill: var(--brand-red); }
  .address {
    position: absolute; left: 0; right: 0; top: 294px;
    text-align: center; color: var(--ink-muted); font-size: 16px;
  }

  /* Back card */
  .card--back {
    left: 388px; top: 505px; width: 566px; height: 352px;
    background: var(--brand-red);
  }
  .emboss {
    position: absolute; left: 142px; top: 30px; width: 290px; height: 290px;
    border-radius: 50%; background: var(--brand-red-deep);
    box-shadow: inset 1px 1px 2px rgba(0,0,0,.15), inset -1px -1px 2px rgba(255,255,255,.08);
  }
  .card--back .brand { left: 102px; top: 123px; }
  .card--back .brand__dot { width: 110px; height: 110px; background: var(--ink-light); margin-right: 14px; }
  .card--back .brand__name { font-size: 70px; color: var(--ink-light); padding-bottom: 12px; }

  .values { position: absolute; left: 0; right: 0; top: 266px; text-align: center; color: var(--ink-light); font-size: 15.5px; }
  .values__row { list-style: none; display: flex; justify-content: center; gap: 5px; line-height: 30px; }
  .values__row li::before {
    content: ""; display: inline-block; width: 8px; height: 8px; border-radius: 50%;
    background: var(--ink-light); margin-right: 6px; vertical-align: 2px;
  }
</style>
</head>
<body>
  <section class="card card--front" aria-label="Business card front">
    <div class="brand">
      <span class="brand__dot"></span>
      <span class="brand__name">quorva</span>
    </div>
    <div class="person">
      <p class="person__name">DANIEL REYES</p>
      <p class="person__role">Managing Director</p>
    </div>
    <ul class="contact">
      <li class="contact__item">
        <svg class="contact__icon" viewBox="0 0 24 24" aria-hidden="true"><path d="M6.6 10.8a15.1 15.1 0 0 0 6.6 6.6l2.2-2.2c.3-.3.7-.4 1-.2 1.1.4 2.3.6 3.6.6.6 0 1 .4 1 1V20c0 .6-.4 1-1 1A17 17 0 0 1 3 4c0-.6.4-1 1-1h3.5c.6 0 1 .4 1 1 0 1.3.2 2.5.6 3.6.1.3 0 .7-.2 1z"/></svg>
        555 014 7396
      </li>
      <li class="contact__item">
        <svg class="contact__icon" viewBox="0 0 24 24" aria-hidden="true"><path d="M12 2a10 10 0 1 0 0 20 10 10 0 0 0 0-20zm6.9 6h-3a15.7 15.7 0 0 0-1.4-3.6A8 8 0 0 1 18.9 8zM12 4c.8 1.2 1.5 2.5 1.9 4h-3.8c.4-1.5 1.1-2.8 1.9-4zM4.3 14a8 8 0 0 1 0-4h3.4a16.5 16.5 0 0 0 0 4zm.8 2h3a15.7 15.7 0 0 0 1.4 3.6A8 8 0 0 1 5.1 16zM8 8H5.1a8 8 0 0 1 4.3-3.6C8.9 5.5 8.4 6.7 8 8zm4 12c-.8-1.2-1.5-2.5-1.9-4h3.8c-.4 1.5-1.1 2.8-1.9 4zm2.3-6H9.7a14.7 14.7 0 0 1 0-4h4.6a14.7 14.7 0 0 1 0 4zm.3 5.6c.6-1.1 1.1-2.3 1.4-3.6h3a8 8 0 0 1-4.4 3.6zm1.7-5.6a16.5 16.5 0 0 0 0-4h3.4a8 8 0 0 1 0 4z"/></svg>
        www.quorva-pay.com
      </li>
    </ul>
    <p class="address">4172 Marlowe blvd, Fernhollow, CA 90299</p>
  </section>

  <section class="card card--back" aria-label="Business card back">
    <span class="emboss" aria-hidden="true"></span>
    <div class="brand">
      <span class="brand__dot"></span>
      <span class="brand__name">quorva</span>
    </div>
    <div class="values">
      <ul class="values__row">
        <li>INNOVATIVE</li><li>PROFESSIONA EXPERT</li><li>HIGH TECH</li><li>TRUST</li>
      </ul>
      <ul class="values__row">
        <li>ONLINE PAYMENT EXPERT</li><li>SECURITY</li>
      </ul>
    </div>
  </section>
</body>
</html>
```